Specialist Recruitment Process Outsourcing (RPO) company needs a modern, sleek website

We need a website which showcases our service offering, describes our onshore and offshore options. Our service is basically building teams of recruiters who become the outsourced (but in-house) recruiter for that specific client. Our logo colours include a light, bright green and a dark/midnight blue. This company will be targeting companies who need help with recruitment in technology, finance, engineering and other white collar industries. We are looking for a look and feeling that communicates cutting edge technology with a bright, energetic appeal. I will include some logo design files to work with.

Target Market(s)

Businesses: start ups who need to grow their staff, SMEs with regular recruitment needs, and larger businesses

Industry/Entity Type

Recruitment

Coding

Coded - Design and coding required

Number of Pages Required

4 page

Font styles to use
Sans Serif

Requirements
Must have
• Landing page should be highly visual, either with dynamic image or scrolling stills accompanies by our core service offering, values, and benefits.

A Services page will allows more detail about what we do, with a call to action.

A User Stories page will showcase some examples of how our services will help certain types of businesses.

Onshore/Offshore page will breakdown the benefits of both approaches and how combinations can work well.

Should fit the colour theming of our logo (files uploaded).

Nice to have
• Imagery can be both around business and people. We are looking for more of a "startup" feel than a corporate-y feel.

```html
<!DOCTYPE html>
<html lang="en">
<head>
<meta charset="utf-8">
<title>Hirewave</title>
<link href="https://fonts.googleapis.com/css2?family=Montserrat:wght@400;500;600&family=Arimo:wght@400&display=swap" rel="stylesheet">
<style>
:root{
  --green:#2ef596;
  --ink:#232325;
  --text:#555;
  --muted:#777;
  --light:#f1f1f1;
  --white:#fff;
}
*{margin:0;padding:0;box-sizing:border-box}
html,body{width:1200px;height:3568px;overflow:hidden}
body{position:relative;background:var(--white);font-family:"Montserrat",sans-serif;color:var(--ink)}
.abs{position:absolute}
.center{left:0;width:1200px;text-align:center}
.brand{font-family:"Montserrat",sans-serif;font-weight:500;color:var(--green);letter-spacing:5px}
/* hero */
.hero{left:0;top:0;width:1200px;height:760px;background:linear-gradient(135deg,#3a3530 0%,#2a2622 45%,#1c1b1a 100%)}
.hero-cut{left:0;top:680px;width:1200px;height:80px}
.nav{top:66px;left:530px;display:flex;gap:50px;font-size:15px;font-weight:500;color:var(--white)}
.nav .active{color:var(--green)}
.hero-logo{top:112px;left:112px;font-size:22px}
.hero-logo .dot{display:inline-block;width:14px;height:14px;border-radius:50%;background:var(--green);margin-right:10px}
.hero-title{top:305px;font-size:64px;font-weight:400;color:var(--green)}
.hero-sub{top:400px;font-size:15px;font-weight:500;color:var(--white);line-height:29px}
.btn-outline{top:482px;left:513px;width:174px;height:58px;border:2px solid var(--green);border-radius:30px;color:var(--green);font-size:15px;display:flex;align-items:center;justify-content:center}
/* section heading */
.sec-title{font-size:39px;font-weight:500;color:var(--ink)}
.sec-title span{color:var(--green)}
.rule{height:3px;width:52px;background:var(--green)}
.svc h3{font-size:18px;font-weight:500;color:var(--ink);text-align:center}
.svc p{font-family:"Arimo",sans-serif;font-size:13.5px;color:var(--muted);line-height:25px;text-align:center;margin-top:10px}
/* values */
.values-bg{left:0;top:1567px;width:1200px;height:563px;background:var(--light)}
.values-green{left:0;top:1567px;width:410px;height:563px;background:var(--green)}
.photo-frame{left:171px;top:1628px;width:434px;height:559px;background:var(--white);border:1px solid #ddd;padding:6px}
.photo{width:100%;height:100%;background:linear-gradient(160deg,#4b3a2c 0%,#2b2320 50%,#6b5a48 100%)}
.values-copy{left:645px;top:1722px;width:444px;font-family:"Arimo",sans-serif;font-size:13.5px;line-height:25px;color:var(--text);text-align:justify}
.ticks{left:648px;top:1870px;list-style:none;font-family:"Arimo",sans-serif;font-size:13.5px;color:var(--text)}
.ticks li{height:43px;display:flex;align-items:center;gap:16px}
/* benefits */
.card{top:2387px;width:307px;height:303px;border:1px solid #e6e6e6;border-radius:6px;background:var(--white);box-shadow:0 1px 4px rgba(0,0,0,.05);text-align:center}
.card .icon{width:123px;height:123px;border-radius:50%;background:var(--green);margin:24px auto 0;display:flex;align-items:center;justify-content:center}
.card h3{font-size:18px;font-weight:500;margin-top:22px}
.card p{font-family:"Arimo",sans-serif;font-size:13.5px;line-height:25px;color:var(--muted);margin-top:8px;padding:0 30px}
/* contact */
.contact-bg{left:0;top:2752px;width:1200px;height:483px;background:linear-gradient(180deg,#f3f3f3,#e9e9e9)}
.field{background:var(--white);border:1px solid #d8d8d8;font-size:11px;font-weight:600;color:#777;padding:17px 14px}
.btn-fill{top:3117px;left:512px;width:171px;height:54px;border-radius:28px;background:var(--green);color:var(--white);font-size:15px;font-weight:500;display:flex;align-items:center;justify-content:center}
/* footer */
.footer{left:0;top:3235px;width:1200px;height:333px;background:var(--ink)}
.foot-nav{top:3392px;left:0;width:1200px;display:flex;justify-content:center;gap:66px;font-size:13px;font-weight:500;color:var(--white)}
.socials{top:3438px;left:0;width:1200px;display:flex;justify-content:center;gap:9px}
.socials span{width:38px;height:38px;border-radius:50%;background:var(--green)}
.copy{top:3502px;font-size:14px;color:var(--white)}
</style>
</head>
<body>

<!-- Hero -->
<div class="abs hero" role="img" aria-label="Photo of a team meeting around a table in an office"></div>
<svg class="abs hero-cut" width="1200" height="80" viewBox="0 0 1200 80">
  <polygon points="0,80 0,77 830,30 1200,0 1200,80" fill="#fff"/>
  <polygon points="830,30 1200,0 1200,80" fill="#2ef596"/>
</svg>
<div class="abs hero-logo brand"><span class="dot"></span>HIREWAVE</div>
<nav class="abs nav"><span class="active">HOME</span><span>SERVICE</span><span>VALUES</span><span>BENEFITS</span><span>CONTACT US</span></nav>
<h1 class="abs center hero-title">HIREWAVE</h1>
<p class="abs center hero-sub">SED UT PERSPICIATIS UNDE OMNIS ISTE NATUS ERROR SIT VOLUPTATEM<br>ACCUSANTIUM DOLOREMQUE LAUDANTIUM</p>
<div class="abs btn-outline">READ MORE</div>

<!-- Core service -->
<h2 class="abs center sec-title" style="top:793px">OUR CORE <span>SERVICE</span></h2>
<div class="abs rule" style="top:853px;left:574px"></div>

<div class="abs svc" style="top:897px;left:450px;width:300px"><h3>CONSULTING</h3><p>Sed ut perspiciatis unde omnis iste<br>natus error sit voluptatem</p></div>
<div class="abs svc" style="top:1178px;left:100px;width:300px"><h3>ASSESSMENT</h3><p>Sed ut perspiciatis unde omnis iste<br>natus error sit voluptatem</p></div>
<div class="abs svc" style="top:1180px;left:797px;width:300px"><h3>RECRUITMENT</h3><p>Sed ut perspiciatis unde omnis iste<br>natus error sit voluptatem</p></div>
<div class="abs svc" style="top:1437px;left:450px;width:300px"><h3>HR OUTSOURCING</h3><p>Sed ut perspiciatis unde omnis iste<br>natus error sit voluptatem</p></div>

<svg class="abs" style="left:380px;top:987px" width="440" height="440" viewBox="0 0 440 440">
  <g fill="#2ef596">
    <rect x="155" y="25" width="130" height="130" rx="18" transform="rotate(45 220 90)"/>
    <rect x="155" y="285" width="130" height="130" rx="18" transform="rotate(45 220 350)"/>
    <rect x="25" y="155" width="130" height="130" rx="18" transform="rotate(45 90 220)"/>
    <rect x="285" y="155" width="130" height="130" rx="18" transform="rotate(45 350 220)"/>
  </g>
  <circle cx="220" cy="220" r="82" fill="#fff"/>
  <circle cx="220" cy="220" r="76" fill="#232325"/>
  <g fill="none" stroke="#232325" stroke-width="3" stroke-linecap="round">
    <circle cx="220" cy="85" r="28"/><circle cx="220" cy="78" r="9"/><path d="M205 100c3-10 27-10 30 0"/><path d="M240 105l14 14"/>
    <path d="M62 240v-40h10v40M80 240v-30h10v30M98 240v-50h10v50M56 242h60"/>
    <circle cx="360" cy="205" r="22"/><path d="M338 205h44M360 183c-10 12-10 32 0 44M360 183c10 12 10 32 0 44"/><path d="M320 260c2-16 14-24 26-24"/>
    <circle cx="195" cy="322" r="7"/><circle cx="220" cy="322" r="7"/><circle cx="245" cy="322" r="7"/><circle cx="220" cy="368" r="20"/><circle cx="220" cy="362" r="6"/>
  </g>
</svg>

<!-- Values -->
<div class="abs values-bg"></div>
<div class="abs values-green"></div>
<div class="abs photo-frame"><div class="photo" role="img" aria-label="Photo of a smiling businesswoman using a tablet"></div></div>
<h2 class="abs sec-title" style="top:1633px;left:640px">OUR <span>VALUES</span></h2>
<div class="abs rule" style="top:1690px;left:642px;background:var(--ink)"></div>
<p class="abs values-copy">Sed ut perspiciatis unde omnis iste natus error sit voluptatem accu santium doloremque laudantium, totam rem aperiam, eaque ipsa quae ab illo inventore veritatis et quasi architecto beatae vitae dicta sunt explicabo. Nemo enim ipsam voluptatem quia voluptas sit eos qui ratione volup unde omnis iste natus error sit tatem sequi nesciunt.</p>
<ul class="abs ticks">
  <li><svg width="13" height="10" viewBox="0 0 13 10"><path d="M1 5l4 4 7-8" fill="none" stroke="#2ef596" stroke-width="2.5"/></svg>Sed ut perspiciatis unde omnis iste natus error</li>
  <li><svg width="13" height="10" viewBox="0 0 13 10"><path d="M1 5l4 4 7-8" fill="none" stroke="#2ef596" stroke-width="2.5"/></svg>sit voluptatem accu santium doloremque</li>
  <li><svg width="13" height="10" viewBox="0 0 13 10"><path d="M1 5l4 4 7-8" fill="none" stroke="#2ef596" stroke-width="2.5"/></svg>laudantium, totam rem aperiam, eaque</li>
  <li><svg width="13" height="10" viewBox="0 0 13 10"><path d="M1 5l4 4 7-8" fill="none" stroke="#2ef596" stroke-width="2.5"/></svg>ipsa quae ab illo inventore veritatis et quasi</li>
  <li><svg width="13" height="10" viewBox="0 0 13 10"><path d="M1 5l4 4 7-8" fill="none" stroke="#2ef596" stroke-width="2.5"/></svg>architecto beatae vitae dicta sunt explicabo</li>
</ul>

<!-- Benefits -->
<h2 class="abs center sec-title" style="top:2277px">FEATURES <span>BENEFITS</span></h2>
<div class="abs rule" style="top:2337px;left:574px"></div>
<div class="abs card" style="left:111px"><div class="icon"><svg width="60" height="60" viewBox="0 0 60 60" fill="none" stroke="#fff" stroke-width="2.5"><rect x="8" y="8" width="14" height="14"/><rect x="8" y="30" width="14" height="14"/><path d="M11 15l3 3 6-7M11 37l3 3 6-7"/><circle cx="42" cy="14" r="6"/><path d="M32 52V28h20v24"/></svg></div><h3>BENEFIT 01</h3><p>Sed ut perspiciatis unde omnis iste natus error sit voluptatem accusantium doloremque laudantium</p></div>
<div class="abs card" style="left:446px"><div class="icon"><svg width="60" height="60" viewBox="0 0 60 60" fill="none" stroke="#fff" stroke-width="2.5"><circle cx="30" cy="22" r="14"/><circle cx="30" cy="22" r="5"/><path d="M24 36v16M36 36v16M24 52h12"/></svg></div><h3>BENEFIT 02</h3><p>Sed ut perspiciatis unde omnis iste natus error sit voluptatem accusantium doloremque laudantium</p></div>
<div class="abs card" style="left:781px"><div class="icon"><svg width="60" height="60" viewBox="0 0 60 60" fill="none" stroke="#fff" stroke-width="2.5"><circle cx="32" cy="28" r="20"/><circle cx="32" cy="28" r="12"/><circle cx="32" cy="28" r="4"/><path d="M32 28l18-18"/></svg></div><h3>BENEFIT 03</h3><p>Sed ut perspiciatis unde omnis iste natus error sit voluptatem accusantium doloremque laudantium</p></div>

<!-- Contact -->
<div class="abs contact-bg"></div>
<h2 class="abs center sec-title" style="top:2804px">CONTACT <span>US</span></h2>
<div class="abs rule" style="top:2866px;left:574px"></div>
<div class="abs field" style="left:278px;top:2906px;width:312px;height:47px">FIRST NAME:</div>
<div class="abs field" style="left:604px;top:2906px;width:313px;height:47px">LAST NAME:</div>
<div class="abs field" style="left:278px;top:2964px;width:312px;height:47px">EMAIL :</div>
<div class="abs field" style="left:604px;top:2964px;width:313px;height:47px">PHONE :</div>
<div class="abs field" style="left:278px;top:3023px;width:639px;height:70px">MESSAGE :</div>
<div class="abs btn-fill">SUBMIT</div>

<!-- Footer -->
<div class="abs footer"></div>
<div class="abs center brand" style="top:3344px;font-size:22px">HIREWAVE</div>
<nav class="abs foot-nav"><span>HOME</span><span>SERVICE</span><span>VALUES</span><span>BENEFITS</span><span>CONTACT US</span></nav>
<div class="abs socials"><span></span><span></span><span></span><span></span></div>
<p class="abs center copy">© Copyrights 2020-Hirewave.All Rights Reserved.</p>

</body>
</html>
```